Business card for a new cabinet shop company named Veloran Cabinets for high end cabinets

Design a business card, thinking dark rich green with colours to speak of high end luxury ie; cream, gold, black possibly

Mitchell Tarrowby
Director Craftsman
Email: info@veloranjoinery-example.com.au
Instagram : @veloran.cabinets

```html
<!DOCTYPE html>
<html lang="en">
<head>
<meta charset="utf-8">
<title>Veloran Cabinets – Business Card</title>
<link href="https://fonts.googleapis.com/css2?family=Montserrat:wght@400;500;700&display=swap" rel="stylesheet">
<style>
  :root {
    --backdrop: #9a9a9a;
    --card: #000000;
    --gold: #c9a86a;
    --cream: #ffffff;
  }
  * { margin: 0; padding: 0; box-sizing: border-box; }
  html, body {
    width: 1200px; height: 1059px; overflow: hidden;
    background: var(--backdrop);
    font-family: "Montserrat", sans-serif;
  }
  .canvas { position: relative; width: 1200px; height: 1059px; }
  .card {
    position: absolute;
    background: var(--card);
    border-radius: 27px;
  }
  .card--front { left: 256px; top: 86px; width: 695px; height: 397px; }
  .card--back  { left: 254px; top: 569px; width: 703px; height: 400px; }

  .wordmark {
    position: absolute;
    display: flex; align-items: center;
    color: var(--gold);
    font-weight: 500;
    white-space: nowrap;
  }
  .wordmark__square { border: 3px solid var(--gold); flex: none; }
  .card--front .wordmark { right: 44px; top: 60px; font-size: 30px; gap: 16px; }
  .card--front .wordmark__square { width: 34px; height: 34px; }
  .card--back .wordmark { left: 50%; top: 50%; transform: translate(-50%, -50%); font-size: 44px; gap: 24px; }
  .card--back .wordmark__square { width: 52px; height: 52px; border-width: 4px; }

  .person { position: absolute; left: 53px; top: 237px; }
  .person__name { color: var(--gold); font-weight: 700; font-size: 31px; line-height: 1; letter-spacing: 0.2px; }
  .person__role { color: var(--cream); font-weight: 400; font-size: 18px; margin-top: 8px; margin-left: 2px; }

  .divider { position: absolute; left: 53px; right: 43px; top: 313px; height: 1.5px; background: var(--cream); }

  .contacts {
    position: absolute; left: 53px; right: 43px; top: 340px;
    display: flex; justify-content: space-between; align-items: center;
    color: var(--cream); font-size: 16px; font-weight: 400;
  }
  .contact { display: flex; align-items: center; gap: 9px; }
  .contact__icon { flex: none; }
  .contact__dot { width: 15px; height: 15px; border-radius: 50%; border: 2px solid var(--gold); }
</style>
</head>
<body>
<main class="canvas">
  <section class="card card--front" aria-label="Card front">
    <div class="wordmark"><span class="wordmark__square"></span><span>Veloran Cabinets</span></div>
    <div class="person">
      <h1 class="person__name">Mitchell Tarrowby</h1>
      <p class="person__role">Director Craftsman</p>
    </div>
    <div class="divider"></div>
    <div class="contacts">
      <div class="contact">
        <svg class="contact__icon" width="18" height="13" viewBox="0 0 18 13" aria-hidden="true">
          <rect width="18" height="13" rx="1" fill="var(--gold)"/>
          <path d="M1 1.5 L9 7.5 L17 1.5" fill="none" stroke="#000" stroke-width="1.6"/>
        </svg>
        <span>info@veloranjoinery-example.com.au</span>
      </div>
      <div class="contact">
        <span class="contact__icon contact__dot"></span>
        <span>@veloran.cabinets</span>
      </div>
    </div>
  </section>

  <section class="card card--back" aria-label="Card back">
    <div class="wordmark"><span class="wordmark__square"></span><span>Veloran Cabinets</span></div>
  </section>
</main>
</body>
</html>
```